Business Card Design

We require a business card design for a law firm, our signature colours are maroon and cream. Our slogan is "From our family to yours", we would like the cards to be professional however feminine at the same time.

Industry/Entity Type

Business

Contact Information for Business Card

Helena Drace & Associates Lawyers & Conveyancers, Helena Drace LL.B. Principal Solicitor, 17 Kellow Street, Marrick NSW 2299

Logo styles of interest
Emblem Logo
Abstract Logo
Wordmark Logo

```html
<!DOCTYPE html>
<html lang="en">
<head>
<meta charset="utf-8">
<title>Helena Drace &amp; Associates — Business Card</title>
<link rel="stylesheet" href="https://fonts.googleapis.com/css2?family=Alegreya+Sans:wght@800&family=Belleza&display=swap">
<style>
  :root {
    --cream-light: #fbf7ee;
    --cream: #f1e9d8;
    --cream-edge: #e8dcc6;
    --ornament: #9d8577;
    --ornament-soft: #b9a397;
    --ink: #141210;
  }
  * { margin: 0; padding: 0; box-sizing: border-box; }
  html, body { width: 1200px; height: 742px; overflow: hidden; }
  body { background: var(--cream); }
  .card {
    position: relative;
    width: 1200px;
    height: 742px;
    overflow: hidden;
    background: radial-gradient(ellipse at 45% 45%, var(--cream-light) 0%, var(--cream) 65%, var(--cream-edge) 100%);
    color: var(--ink);
  }
  .ornament {
    position: absolute;
    background: linear-gradient(180deg, var(--ornament-soft), var(--ornament));
    opacity: 0.55;
    border-radius: 40px;
  }
  .divider-top { left: 97px; top: 84px; width: 383px; height: 20px; }
  .divider-bottom { left: 713px; top: 634px; width: 390px; height: 20px; }
  .scales { left: 119px; top: 400px; width: 281px; height: 260px; border-radius: 50% 50% 30% 30%; }
  .flourish { left: 789px; top: 119px; width: 389px; height: 184px; border-radius: 50%; }

  .firm-name {
    position: absolute;
    left: 98px;
    top: 158px;
    font-family: "Alegreya Sans", sans-serif;
    font-weight: 800;
    font-size: 55px;
    line-height: 70px;
    letter-spacing: 0.3px;
  }
  .firm-tagline {
    position: absolute;
    left: 100px;
    top: 318px;
    font-family: "Belleza", sans-serif;
    font-size: 31px;
    letter-spacing: 0.5px;
  }
  .contact {
    position: absolute;
    right: 97px;
    top: 328px;
    text-align: right;
    font-family: "Belleza", sans-serif;
    font-size: 38px;
    line-height: 56px;
    letter-spacing: 1px;
    font-style: normal;
  }
</style>
</head>
<body>
  <main class="card">
    <div class="ornament divider-top" role="img" aria-label="Scrolled line divider ornament"></div>

    <h1 class="firm-name">Helena Drace<br>&amp; Associates</h1>
    <p class="firm-tagline">Lawyers &amp; Conveyancers</p>

    <div class="ornament scales" role="img" aria-label="Decorative scales of justice illustration"></div>

    <div class="ornament flourish" role="img" aria-label="Calligraphic flourish ornament"></div>

    <address class="contact">
      Helena Drace<br>
      LL.B. Principal Solicitor<br>
      17 Kellow Street<br>
      Marrick NSW 2299
    </address>

    <div class="ornament divider-bottom" role="img" aria-label="Scrolled line divider ornament"></div>
  </main>
</body>
</html>
```